Velmora Cabinets Letter Head and Email Signature

Hi
I would love a design package for a letterhead, email signature, even update my business card if you like if you can come up with a great idea for my new high end cabinet shop. Velmora Cabinets brings timeless craftsmanship to modern interiors, specializing in high end, custom cabinetry designed for architects and interior designers.

Target Market(s)

high end, luxury market

Industry/Entity Type

cabinet making

Requirements
Must have
• my colours of logo as the theme

```html
<!DOCTYPE html>
<html lang="en">
<head>
<meta charset="utf-8">
<title>Velmora Cabinets – Stationery</title>
<link href="https://fonts.googleapis.com/css2?family=Poppins:wght@300;400;500;600;700&display=swap" rel="stylesheet">
<style>
:root{
  --bg:#c9c9c9;
  --green:#4a7c4a;
  --black:#000;
  --ink:#1a1a1a;
  --paper:#fff;
  --light-grey:#e8e8e8;
  --band:#161616;
  --label:#2b2b2b;
}
*{margin:0;padding:0;box-sizing:border-box}
html,body{width:1200px;height:2962px;overflow:hidden}
body{background:var(--bg);font-family:'Poppins',sans-serif;color:var(--ink);position:relative}
.piece{position:absolute;overflow:hidden;box-shadow:0 14px 22px rgba(0,0,0,.28)}
.abs{position:absolute}
.layer{position:absolute;left:0;top:0}
.label{position:absolute;left:0;width:1200px;text-align:center;font-weight:700;font-size:57px;color:var(--label);letter-spacing:.5px}

/* wordmark */
.wordmark .name{font-weight:400;color:var(--green);line-height:1;letter-spacing:1px}
.wordmark .sub{font-weight:400;line-height:1;letter-spacing:.36em}

/* letterhead */
.letterhead{left:232px;top:133px;width:736px;height:952px;background:var(--paper)}
.lh-sender{left:48px;top:222px}
.lh-sender h2{font-size:22px;font-weight:600;color:var(--black);margin-bottom:10px}
.lh-sender p{font-size:12.5px;line-height:16px;color:var(--ink)}
.lh-sender b{color:var(--green);font-weight:600}
.lh-sender .indent{padding-left:21px}
.lh-date{right:48px;top:313px;font-size:13.5px}
.lh-date b{color:var(--green);font-weight:600}
.lh-body{left:48px;top:370px;width:640px}
.lh-body h3{font-size:17px;font-weight:500;color:var(--black);margin-bottom:8px}
.lh-body p{font-size:10.4px;line-height:13px;margin-bottom:13px;color:var(--ink)}
.lh-signoff{left:48px;top:712px}
.lh-signoff .yours{font-size:12px;font-weight:600}
.lh-signoff .who{font-size:19px;font-weight:500;margin-top:10px}
.lh-signoff .role{font-size:12px;font-weight:500}
.lh-footer{left:48px;top:891px;display:flex;gap:24px;font-size:15px}
.contact{display:flex;align-items:center;gap:6px;white-space:nowrap}
.dot{width:16px;height:16px;border-radius:50%;background:var(--green);display:inline-flex;align-items:center;justify-content:center;flex:none}

/* dark pieces */
.card{width:737px;height:421px;background:var(--black);color:var(--paper)}
.card-front{left:232px;top:1300px}
.card-back{left:232px;top:1783px}
.signature{left:167px;top:2433px;width:868px;height:288px;background:var(--black);color:var(--paper)}
.dark-band{position:absolute;left:0;right:0;bottom:0;background:var(--band)}
.pattern{position:absolute;right:0;top:0;height:100%;background:linear-gradient(90deg,rgba(0,0,0,0) 0%,rgba(70,70,70,.55) 60%,rgba(120,120,120,.6) 100%)}
.person .who{color:var(--green);font-weight:700;line-height:1}
.contacts{position:absolute;display:flex;flex-direction:column}
.contacts .contact{color:var(--paper)}
</style>
</head>
<body>

<!-- ===== Letterhead ===== -->
<section class="piece letterhead">
  <div class="abs" role="img" aria-label="Faint hexagon line pattern" style="left:420px;top:0;width:316px;height:230px;background:linear-gradient(200deg,rgba(0,0,0,.05),rgba(0,0,0,0) 70%)"></div>
  <div class="abs" role="img" aria-label="Faint hexagon line pattern" style="left:0;top:700px;width:300px;height:160px;background:linear-gradient(20deg,rgba(0,0,0,.05),rgba(0,0,0,0) 70%)"></div>
  <svg class="layer" width="736" height="952" viewBox="0 0 736 952">
    <polygon points="0,0 440,0 352,148 0,148" fill="var(--light-grey)"/>
    <polygon points="432,64 736,64 736,108 406,108" fill="var(--green)"/>
    <polyline points="239,154 360,154 421,51" fill="none" stroke="var(--black)" stroke-width="6"/>
    <polygon points="0,864 736,864 736,952 0,952" fill="var(--light-grey)"/>
    <polygon points="0,936 736,936 736,952 0,952" fill="var(--black)"/>
    <polygon points="680,908 736,908 736,952 650,952" fill="var(--black)"/>
    <polyline points="550,942 662,942 715,855" fill="none" stroke="var(--green)" stroke-width="6"/>
  </svg>
  <div class="abs wordmark" style="left:50px;top:45px">
    <div class="name" style="font-size:40px">Velmora</div>
    <div class="sub" style="font-size:17px;color:var(--black);margin-top:4px">CABINETS</div>
  </div>
  <div class="abs lh-sender">
    <h2>Owen Harcourt</h2>
    <p><b>P :</b> 0412 386 590</p>
    <p style="margin-top:4px"><b>A :</b> Alder Street, lane no.214</p>
    <p class="indent">Mill Road - KR2087</p>
    <p style="margin-top:4px"><b>W :</b> www.velmora.com</p>
  </div>
  <div class="abs lh-date"><b>Issuing Date:</b> May 5, 2018</div>
  <div class="abs lh-body">
    <h3>Dear Contributor,</h3>
    <p>Thank you for your continued support of our workshop this season. Every cabinet we build begins with a careful conversation about how a room will be used, the light it receives and the materials that will age gracefully within it. Our team of joiners and finishers works from detailed drawings prepared alongside architects and interior designers, so that each piece arrives on site ready to fit with precision. We select timbers from responsible suppliers and finish every surface by hand before it leaves the workshop floor.</p>
    <p>This year we expanded our finishing room and added a second spray booth, which allows us to deliver lacquered and veneered joinery on shorter timelines without compromising quality. We have also introduced a new range of brass and blackened steel hardware, made in small batches by a local foundry, to complement our kitchen, wardrobe and library cabinetry.</p>
    <p>Samples of each finish are available in our showroom, and we would be glad to arrange a private viewing for you and your clients at a time that suits.</p>
    <p>As always, our commitment extends well beyond installation. Every project is documented with a care guide that explains how to clean, protect and maintain the finishes we apply, and our team remains available for adjustments in the years that follow. We believe fine cabinetry should improve with time, and we stand behind the work we deliver. Should you have a project in planning, please send through your drawings or schedule a visit to the workshop, where we can talk through joinery details, material options and lead times in person.</p>
  </div>
  <div class="abs lh-signoff">
    <div class="yours">Yours Sincerely</div>
    <div class="who">Owen Harcourt</div>
    <div class="role">Director Craftsman</div>
  </div>
  <div class="abs lh-footer">
    <span class="contact"><span class="dot"><svg width="9" height="9" viewBox="0 0 10 10"><path d="M2 1l2 2-1 1.3c.6 1.2 1.5 2.1 2.7 2.7L7 6l2 2-1.2 1.4C4.5 9 1 5.5.6 2.2z" fill="#fff"/></svg></span>0412 386 590</span>
    <span class="contact"><span class="dot"><svg width="9" height="7" viewBox="0 0 10 8"><rect width="10" height="8" rx="1" fill="#fff"/><path d="M0 1l5 3.5L10 1" stroke="var(--green)" fill="none"/></svg></span>info@velmoracabinets.com.au</span>
    <span class="contact" style="margin-left:8px"><span class="dot"></span>@velmora.cabinets</span>
  </div>
</section>
<div class="label" style="top:1138px">Letterhead</div>

<!-- ===== Business card front ===== -->
<section class="piece card card-front">
  <div class="pattern" role="img" aria-label="Repeating outlined cabinet pattern in grey" style="width:400px"></div>
  <svg class="layer" width="737" height="421" viewBox="0 0 737 421">
    <polygon points="91,33 336,33 355,0 375,0 344,48 91,48" fill="var(--paper)"/>
    <polygon points="344,20 737,20 737,36 334,36" fill="var(--green)"/>
    <polygon points="335,386 570,386 676,215 690,215 584,400 335,400" fill="var(--green)"/>
    <polygon points="547,421 618,309 737,309 737,421" fill="var(--paper)"/>
  </svg>
  <div class="abs wordmark" style="left:242px;top:152px">
    <div class="name" style="font-size:72px">Velmora</div>
    <div class="sub" style="font-size:35px;color:var(--paper);margin-top:8px">CABINETS</div>
  </div>
</section>

<!-- ===== Business card back ===== -->
<section class="piece card card-back">
  <div class="dark-band" style="top:246px"></div>
  <div class="pattern" role="img" aria-label="Repeating outlined cabinet pattern in grey" style="width:430px"></div>
  <svg class="layer" width="737" height="421" viewBox="0 0 737 421">
    <polygon points="335,386 570,386 676,215 690,215 584,400 335,400" fill="var(--green)"/>
    <polygon points="547,421 618,309 737,309 737,421" fill="var(--paper)"/>
  </svg>
  <div class="abs wordmark" style="left:125px;top:46px">
    <div class="name" style="font-size:40px">Velmora</div>
    <div class="sub" style="font-size:19px;color:var(--paper);margin-top:4px">CABINETS</div>
  </div>
  <div class="abs person" style="left:58px;top:162px">
    <div class="who" style="font-size:40px">Owen Harcourt</div>
    <div style="font-size:22px;margin-top:8px">Director Craftsman</div>
  </div>
  <div class="contacts" style="left:62px;top:268px;gap:10px;font-size:19px">
    <span class="contact"><span class="dot"><svg width="9" height="9" viewBox="0 0 10 10"><path d="M2 1l2 2-1 1.3c.6 1.2 1.5 2.1 2.7 2.7L7 6l2 2-1.2 1.4C4.5 9 1 5.5.6 2.2z" fill="#fff"/></svg></span>0412 386 590</span>
    <span class="contact"><span class="dot"><svg width="9" height="7" viewBox="0 0 10 8"><rect width="10" height="8" rx="1" fill="#fff"/><path d="M0 1l5 3.5L10 1" stroke="var(--green)" fill="none"/></svg></span>info@velmoracabinets.com.au</span>
    <span class="contact"><span class="dot"></span>@velmora.cabinets</span>
  </div>
</section>
<div class="label" style="top:2262px">Business Card</div>

<!-- ===== Email signature ===== -->
<section class="piece signature">
  <div class="dark-band" style="top:128px"></div>
  <div class="pattern" role="img" aria-label="Repeating outlined cabinet pattern in grey" style="width:260px"></div>
  <svg class="layer" width="868" height="288" viewBox="0 0 868 288">
    <polygon points="75,69 252,69 293,0 313,0 264,82 75,82" fill="var(--paper)"/>
    <polygon points="305,0 868,0 868,15 296,15" fill="var(--green)"/>
    <polygon points="578,255 752,255 826,136 840,136 760,269 578,269" fill="var(--green)"/>
    <polygon points="742,288 797,236 868,236 868,288" fill="var(--paper)"/>
  </svg>
  <div class="abs person" style="left:385px;top:40px">
    <div class="who" style="font-size:31px">Owen Harcourt</div>
    <div style="font-size:18px;letter-spacing:.12em;margin-top:6px">Director Craftsman</div>
  </div>
  <div class="abs wordmark" style="left:160px;top:160px">
    <div class="name" style="font-size:42px">Velmora</div>
    <div class="sub" style="font-size:21px;color:var(--paper);margin-top:6px">CABINETS</div>
  </div>
  <div class="contacts" style="left:385px;top:152px;gap:8px;font-size:18px">
    <span class="contact"><span class="dot"><svg width="9" height="9" viewBox="0 0 10 10"><path d="M2 1l2 2-1 1.3c.6 1.2 1.5 2.1 2.7 2.7L7 6l2 2-1.2 1.4C4.5 9 1 5.5.6 2.2z" fill="#fff"/></svg></span>0412 386 590</span>
    <span class="contact"><span class="dot"><svg width="9" height="7" viewBox="0 0 10 8"><rect width="10" height="8" rx="1" fill="#fff"/><path d="M0 1l5 3.5L10 1" stroke="var(--green)" fill="none"/></svg></span>info@velmoracabinets.com.au</span>
    <span class="contact"><span class="dot"></span>@velmora.cabinets</span>
  </div>
</section>
<div class="label" style="top:2772px">Email Signature</div>

</body>
</html>
```